Weightloss company needs Business Card

We want a business card that is clean and professional, yet portrays that we are a friendly, innovative, and versatile program designed to fit the needs of our clients.
I would like there to be 2 sides, one side having an appointment card, and the other side containing the logo and business information. There can be decorations on both sides. The logo is attached.

Target Market(s)

Men and women 40-60

Industry/Entity Type

Business

Contact Information for Business Card

Font styles to use
Sans Serif

Requirements
Must have
• The logo, space for business information
Nice to have
• The colors in the logo
Should not have
• No pictures of people or food

```html
<!DOCTYPE html>
<html lang="en">
<head>
<meta charset="utf-8">
<title>Renewal Path Wellness – Business Card</title>
<link rel="stylesheet" href="https://fonts.googleapis.com/css2?family=Open+Sans:ital,wght@0,400;0,600;0,700;1,400&display=swap">
<style>
  :root {
    --red: #ef1f54;
    --cyan: #3cc8ec;
    --ink: #4a4a4a;
    --muted: #8a8a8a;
    --card: #ffffff;
    --bg: #e9e7e3;
    --rule: #b8b8b8;
  }
  * { box-sizing: border-box; margin: 0; padding: 0; }
  html, body { width: 1200px; height: 950px; overflow: hidden; }
  body {
    background: var(--bg);
    font-family: "Open Sans", Arial, sans-serif;
    color: var(--ink);
    display: flex;
    align-items: center;
    justify-content: center;
    gap: 40px;
  }
  .card {
    width: 540px;
    height: 310px;
    background: var(--card);
    border-radius: 18px;
    position: relative;
    overflow: hidden;
    box-shadow: 0 6px 18px rgba(0,0,0,.12);
  }

  /* Front */
  .brand {
    position: absolute; left: 34px; top: 34px;
    display: flex; align-items: center; gap: 10px;
    color: var(--red); font-weight: 700; font-size: 30px; letter-spacing: -.5px;
  }
  .brand-dot { width: 16px; height: 16px; border-radius: 50%; background: var(--red); }
  .divider {
    position: absolute; left: 34px; right: 34px; top: 96px;
    height: 1px; background: var(--cyan);
  }
  .person { position: absolute; left: 34px; top: 138px; }
  .person-name { color: var(--red); font-size: 19px; font-weight: 400; letter-spacing: .5px; line-height: 1.1; }
  .person-title { color: var(--cyan); font-size: 13px; letter-spacing: .3px; }
  .contacts { list-style: none; margin-top: 10px; font-size: 13px; line-height: 1.5; }
  .contacts li { display: flex; align-items: center; gap: 8px; }
  .contacts svg { width: 12px; height: 12px; fill: var(--red); }
  .address {
    position: absolute; right: 34px; top: 150px; text-align: right;
    font-size: 14px; line-height: 1.5; color: var(--ink);
  }
  .band {
    position: absolute; left: 0; right: 0; bottom: 0; height: 44px;
    background: var(--red);
    display: flex; align-items: center; padding-left: 34px;
    color: #fff; font-size: 14px; letter-spacing: 2px;
  }
  .band-cap {
    position: absolute; right: 0; top: 0; width: 26px; height: 44px; background: var(--cyan);
  }
  .band-cap::before {
    content: ""; position: absolute; left: -22px; top: 0; width: 44px; height: 44px;
    border-radius: 50%; background: var(--red);
  }

  /* Back */
  .back { padding: 30px 38px; }
  .appt-title { text-align: center; color: var(--red); font-size: 22px; font-weight: 600; }
  .line-row { display: flex; align-items: flex-end; gap: 8px; margin-top: 22px; font-size: 13px; }
  .fill { flex: 1; border-bottom: 1px dotted var(--rule); height: 14px; }
  .days { display: flex; justify-content: space-between; margin-top: 24px; font-size: 13px; color: var(--red); }
  .day { display: flex; align-items: center; gap: 5px; }
  .box { width: 12px; height: 12px; border: 1px solid var(--ink); }
  .time-row { color: var(--red); }
  .time-row .label { color: var(--red); }
  .ampm { font-size: 10px; }
  .note {
    margin-top: 30px; font-style: italic; font-size: 11px; color: var(--ink);
    text-align: center; line-height: 1.5;
  }
</style>
</head>
<body>

<section class="card card-front" aria-label="Front of business card">
  <div class="brand"><span class="brand-dot"></span>Renewal Path Wellness</div>
  <div class="divider"></div>

  <div class="person">
    <p class="person-name">DANIEL HARPER</p>
    <p class="person-title">CEO/FOUNDER</p>
    <ul class="contacts">
      <li><svg viewBox="0 0 24 24"><path d="M6.6 10.8a15.1 15.1 0 0 0 6.6 6.6l2.2-2.2a1 1 0 0 1 1-.25 11.4 11.4 0 0 0 3.6.57 1 1 0 0 1 1 1V20a1 1 0 0 1-1 1A17 17 0 0 1 3 4a1 1 0 0 1 1-1h3.5a1 1 0 0 1 1 1c0 1.25.2 2.45.57 3.57a1 1 0 0 1-.25 1z"/></svg>555 210 4837</li>
      <li><svg viewBox="0 0 24 24"><path d="M7 2h10a1 1 0 0 1 1 1v18a1 1 0 0 1-1 1H7a1 1 0 0 1-1-1V3a1 1 0 0 1 1-1zm1 3v13h8V5z"/></svg>555 318 7720</li>
      <li><svg viewBox="0 0 24 24"><path d="M6 3h12v6h2a1 1 0 0 1 1 1v8h-3v3H6v-3H3v-8a1 1 0 0 1 1-1h2zm2 2v4h8V5zm0 10v4h8v-4z"/></svg>555 462 0193</li>
      <li><svg viewBox="0 0 24 24"><path d="M3 5h18v14H3zm2 2v.5l7 4.5 7-4.5V7zm0 2.9V17h14V9.9l-7 4.5z"/></svg>hello@renewalpath.example</li>
    </ul>
  </div>

  <p class="address">2140 Maple Ridge Road<br>Fairview, Oregon 97024</p>

  <div class="band">www.renewalpath.example<span class="band-cap"></span></div>
</section>

<section class="card back" aria-label="Appointment side of business card">
  <h2 class="appt-title">Next Appointment</h2>
  <div class="line-row"><span class="fill"></span><span>has an appointment</span></div>
  <div class="days">
    <span class="day">Mon<span class="box"></span></span>
    <span class="day">Tue<span class="box"></span></span>
    <span class="day">Wed<span class="box"></span></span>
    <span class="day">Thu<span class="box"></span></span>
    <span class="day">Fri<span class="box"></span></span>
    <span class="day">Sat<span class="box"></span></span>
  </div>
  <div class="line-row time-row"><span class="label">Time :</span><span class="fill"></span><span class="ampm">AM/PM</span></div>
  <p class="note">Please give 24 hours notice if you are unable to keep your appointment or<br>a cancellation fee may be charged.</p>
</section>

</body>
</html>
```